Veterinary Pylon

My veterinary clinic is not clearly visible from the street and I want to place a Pylon next to my driveway. I want a modern, elegant straight Design, the Photo shows the sheduled place. One can see the clinic on our Homepage: www.tailbright-vethaus.at
The last pictures are examples for pylones I like

Target Market(s)

the passing cars often miss my entry...I want to show where to turn left

Colors
3276b5
33a6d7
00a990

Requirements
Must have
• High value, simple elegance, size: 250cm (high) x 100cm (width)
Nice to have
• Our Logo, arrow(?)

A special Text is not necessary but this will be an option:

Biegen sie hier ab und wir biegen es wieder hin!
Should not have
• Too much Color, the colors I have chosen are the possible colors but it‘s not necessary to use them.

```html
<!DOCTYPE html>
<html lang="de">
<head>
<meta charset="utf-8">
<title>Tailbright Vethaus – Pylon</title>
<link rel="stylesheet" href="https://fonts.googleapis.com/css2?family=Archivo+Black&display=swap">
<style>
  :root {
    --navy: #134a93;
    --sky: #2db8dc;
    --paper: #ffffff;
    --mist: #eff3f8;
    --haze: #d9e1ee;
    --arrow: #ffffff;
  }
  html, body {
    margin: 0;
    padding: 0;
    width: 1200px;
    height: 3000px;
    overflow: hidden;
    background: var(--paper);
  }
  .pylon {
    position: relative;
    width: 1200px;
    height: 3000px;
    overflow: hidden;
    background: var(--paper);
  }
  .pylon-backdrop {
    position: absolute;
    inset: 0;
  }
  .emblem-artwork {
    position: absolute;
    left: 210px;
    top: 169px;
    width: 833px;
    height: 495px;
    border-radius: 40px;
    background: linear-gradient(135deg, var(--sky) 0%, var(--navy) 70%);
    opacity: 0.9;
  }
  .clinic-name {
    position: absolute;
    left: 0;
    width: 1200px;
    top: 770px;
    margin: 0;
    text-align: center;
    font-family: "Archivo Black", "Arial Black", sans-serif;
    font-weight: 400;
    color: var(--navy);
    line-height: 1;
    text-transform: uppercase;
  }
  .clinic-name .name-main {
    display: block;
    font-size: 150px;
    letter-spacing: -2px;
  }
  .clinic-name .name-sub {
    display: block;
    margin-top: 40px;
    font-size: 86px;
    letter-spacing: 24px;
  }
  .turn-sign {
    position: absolute;
    left: 356px;
    top: 1395px;
    width: 484px;
    height: 484px;
  }
  .faint-motif {
    position: absolute;
    left: 0;
    top: 2120px;
    width: 1200px;
    height: 816px;
    background: linear-gradient(180deg, var(--haze) 0%, var(--haze) 65%, rgba(217,225,238,0) 100%);
  }
</style>
</head>
<body>
<main class="pylon">
  <svg class="pylon-backdrop" width="1200" height="3000" viewBox="0 0 1200 3000" aria-hidden="true">
    <circle cx="600" cy="2981" r="1268" fill="var(--mist)"/>
  </svg>

  <div class="emblem-artwork" role="img" aria-label="Illustration of a dog and a cat in front of a heart with a heartbeat line"></div>

  <h1 class="clinic-name">
    <span class="name-main">Tailbright</span>
    <span class="name-sub">Vethaus</span>
  </h1>

  <div class="faint-motif" role="img" aria-label="Faint large illustration of a dog and a cat with a heartbeat line"></div>

  <svg class="turn-sign" viewBox="0 0 484 484" role="img" aria-label="Turn left arrow">
    <defs>
      <linearGradient id="sign-fill" x1="0" y1="0" x2="1" y2="0">
        <stop offset="0" stop-color="#134a93"/>
        <stop offset="1" stop-color="#2db8dc"/>
      </linearGradient>
    </defs>
    <circle cx="242" cy="242" r="242" fill="url(#sign-fill)"/>
    <g fill="none" stroke="var(--arrow)" stroke-width="24">
      <line x1="118" y1="242" x2="384" y2="242"/>
      <polyline points="210,134 104,242 210,350"/>
    </g>
  </svg>
</main>
</body>
</html>
```